Awesome photographers card for an awesome new business

Double sided business card Black background and silver logo in middle on one side. Details on otherside. please keep it simple

Industry/Entity Type

Photographer

Contact Information for Business Card

Gerald Fenwick
0452817360
GeraldFenwickPhotography47@mailbox.test
www.GeraldFenwickPhotography.test.au
Instagram _Gerald_fenwick

Requirements
Must have
• My logo in Silver
• please use instagram logo instead of "Instagram"

```html
<!DOCTYPE html>
<html lang="en">
<head>
<meta charset="utf-8">
<title>Gerald Fenwick Photography – Business Card</title>
<link href="https://fonts.googleapis.com/css2?family=Roboto:wght@400;500&family=Roboto+Condensed:wght@700&display=swap" rel="stylesheet">
<style>
  :root {
    --backdrop: #262626;
    --card-front: #f4f4f4;
    --ink: #4a4a4a;
    --ink-strong: #555555;
    --silver-light: #b4b4b4;
    --silver-mid: #8a8a8a;
    --silver-dark: #6a6a6a;
    --silver-text: #f2f2f2;
    --tab-light: #d8d8d8;
    --tab-dark: #5a5a5a;
  }
  * { margin: 0; padding: 0; box-sizing: border-box; }
  html, body {
    width: 1200px; height: 960px; overflow: hidden;
    background: var(--backdrop);
    font-family: "Roboto", Arial, sans-serif;
  }
  .canvas { position: relative; width: 1200px; height: 960px; }

  .card { position: absolute; width: 600px; height: 343px; }

  /* Front: details side */
  .card--front { left: 314px; top: 113px; background: var(--card-front); }
  .card__name {
    position: absolute; right: 44px; top: 40px;
    font-family: "Roboto Condensed", Arial, sans-serif;
    font-weight: 700; font-size: 21px; color: var(--ink-strong);
    letter-spacing: 0.2px;
  }
  .card__tab {
    position: absolute; right: 0; top: 35px; width: 13px; height: 36px;
    background: linear-gradient(90deg, var(--tab-dark), var(--tab-light) 60%, var(--tab-dark));
  }
  .brand {
    position: absolute; display: flex; align-items: center; gap: 10px;
  }
  .brand__dot {
    width: 34px; height: 34px; border-radius: 50%;
    border: 3px solid currentColor; flex: none;
  }
  .brand__name { font-weight: 500; font-size: 19px; line-height: 1.2; }
  .card--front .brand { left: 40px; top: 150px; color: var(--silver-dark); }

  .contacts {
    position: absolute; left: 39px; top: 270px;
    font-size: 14.5px; color: var(--ink); line-height: 19px;
  }
  .contacts__row { display: flex; align-items: center; white-space: nowrap; }
  .contact { display: inline-flex; align-items: center; gap: 7px; margin-right: 6px; }
  .contact svg { width: 14px; height: 14px; fill: var(--ink); flex: none; }
  .contact__mark {
    width: 12px; height: 12px; background: var(--ink); border-radius: 2px; flex: none;
  }

  /* Back: logo side */
  .card--back {
    left: 311px; top: 472px;
    background: radial-gradient(ellipse 55% 90% at 50% 35%, var(--silver-light), var(--silver-mid) 60%, var(--silver-dark));
  }
  .card--back .brand {
    left: 0; right: 0; top: 145px; justify-content: center; color: var(--silver-text);
  }
  .card--back .brand__name { font-size: 22px; }
  .card__url {
    position: absolute; left: 0; right: 0; top: 292px; text-align: center;
    font-size: 14.5px; letter-spacing: 2.2px; color: var(--silver-text);
  }
</style>
</head>
<body>
<main class="canvas">
  <section class="card card--front" aria-label="Business card, details side">
    <h1 class="card__name">GERALD FENWICK</h1>
    <span class="card__tab"></span>
    <div class="brand">
      <span class="brand__dot"></span>
      <span class="brand__name">Gerald Fenwick Photography</span>
    </div>
    <div class="contacts">
      <div class="contacts__row">
        <span class="contact">
          <svg viewBox="0 0 24 24" aria-hidden="true"><path d="M6.6 10.8a15.1 15.1 0 0 0 6.6 6.6l2.2-2.2c.3-.3.7-.4 1-.2 1.1.4 2.3.6 3.6.6.6 0 1 .4 1 1V20c0 .6-.4 1-1 1A17 17 0 0 1 3 4c0-.6.4-1 1-1h3.5c.6 0 1 .4 1 1 0 1.3.2 2.5.6 3.6.1.3 0 .7-.2 1z"/></svg>
          0452817360
        </span>
        <span class="contact">
          <svg viewBox="0 0 24 24" aria-hidden="true"><path d="M2 5h20v14H2z M3 6l9 7 9-7" /></svg>
          GeraldFenwickPhotography47@mailbox.test
        </span>
      </div>
      <div class="contacts__row">
        <span class="contact">
          <svg viewBox="0 0 24 24" aria-hidden="true"><circle cx="12" cy="12" r="10"/></svg>
          www.GeraldFenwickPhotography.test.au
        </span>
        <span class="contact">
          <span class="contact__mark"></span>
          Gerald_fenwick
        </span>
      </div>
    </div>
  </section>

  <section class="card card--back" aria-label="Business card, logo side">
    <div class="brand">
      <span class="brand__dot"></span>
      <span class="brand__name">Gerald Fenwick Photography</span>
    </div>
    <p class="card__url">www.GeraldFenwickPhotography.test.au</p>
  </section>
</main>
</body>
</html>
```